I want to redesign the Tallvex corporate website

Morrowdale Farms Limited (Tallvex) is a Nigerian integrated agribusiness and premium food company operating across agriculture, food processing and nationwide FMCG distribution.
We are redesigning our corporate website to reflect our evolution into a modern, premium food company capable of serving institutional buyers, distributors, retailers, investors and consumers. The new website should feel comparable to the websites of leading global food brands — not a typical agricultural website.

Target Market(s)

Nigeria / Africa

Industry/Entity Type

FMCG

Coding

Coded - Design and coding required

Number of Pages Required

5+ page

Colors

Designer to choose colors to be used in the design.

Requirements
Must have
• The website must communicate the following attributes consistently across every page, in both design and language. Premium Quality of finish signals quality of product , Clean Uncluttered layouts, disciplined use of elements ,Modern Current design language, not dated conventions ,Innovative and Forward-looking, technology-enabled , Sustainable Responsible practice made visible Nigerian with global standards, Proudly local in origin, international in execution
Nice to have
• Lots of white space , Fast loading, Premium photography,Mobile-first,Elegant typography,Minimal clutter, Rounded elements,High-end corporate feel, Smooth curved section transitions, Soft shadows
Should not have
• The new website should feel comparable to the websites of leading global food brands — not a typical agricultural website. Also do not copy the business profile as website , its is just a guide !

```html
<!DOCTYPE html>
<html lang="en">
<head>
<meta charset="utf-8">
<title>Tallvex — Website Redesign Concepts</title>
<link rel="stylesheet" href="https://fonts.googleapis.com/css2?family=Inter:wght@400;500;600;700&family=DM+Serif+Display&family=Caveat:wght@500&display=swap">
<style>
:root{
  --forest:#1f4a1e;
  --forest-deep:#173a17;
  --lime:#8dc63f;
  --lime-bright:#9ccb2f;
  --orange:#c8501a;
  --mist:#f1f5e6;
  --paper:#ffffff;
  --ink:#1d2a1a;
  --muted:#5f6b5a;
}
*{box-sizing:border-box;margin:0;padding:0}
html,body{width:1200px;height:1200px;overflow:hidden;background:#fff}
body{position:relative;font-family:'Inter',sans-serif;color:var(--ink)}
.abs{position:absolute}
.page{position:absolute;top:21px;height:1159px;overflow:hidden}
.page-a{left:314px;width:252px;background:var(--paper)}
.page-b{left:609px;width:284px;background:var(--mist)}
.logo{font-family:'Inter',sans-serif;font-weight:700;color:var(--forest);letter-spacing:-.2px}
.nav-links{display:flex;gap:6px;font-size:2.4px;color:var(--ink);font-weight:500}
.btn{position:absolute;background:var(--orange);color:#fff;font-size:2.3px;font-weight:600;border-radius:4px;display:flex;align-items:center;justify-content:center;gap:2px;white-space:nowrap}
.btn-ghost{position:absolute;border:.5px solid var(--muted);color:var(--ink);font-size:2.3px;font-weight:600;border-radius:2px;display:flex;align-items:center;justify-content:center}
.center{text-align:center;left:0;right:0}
.h-sans{font-weight:700;color:var(--forest);line-height:1.2}
.h-serif{font-family:'DM Serif Display',serif;font-weight:400;color:var(--forest);line-height:1.1}
.tiny{font-size:2.3px;line-height:1.5;color:var(--muted)}
.kicker{font-size:2px;font-weight:700;letter-spacing:.4px;color:var(--orange);text-transform:uppercase}
.script{font-family:'Caveat',cursive}
.photo{position:absolute;overflow:hidden}
.card{position:absolute;background:#fff;border-radius:4px;box-shadow:0 1px 4px rgba(0,0,0,.08)}
.footer-col h4{font-size:2.4px;color:#fff;font-weight:600;margin-bottom:2px}
.footer-col p{font-size:2.1px;color:#d7e3cf;line-height:1.7}
</style>
</head>
<body>

<section class="page page-a">
  <div class="abs" style="top:0;left:0;width:252px;height:4px;background:var(--forest)">
    <div class="abs" style="right:30px;top:.6px;font-size:2px;color:#fff">Investors | News &amp; Media | Careers</div>
  </div>
  <header class="abs" style="top:4px;left:0;width:252px;height:16px;background:#fff">
    <div class="abs logo" style="left:31px;top:3px;font-size:8px">Tallvex</div>
    <div class="abs nav-links" style="left:68px;top:6.5px"><span>Home</span><span>About Us</span><span>Products</span><span>Our Business</span><span>Sustainability</span></div>
    <div class="btn" style="left:198px;top:5px;width:22px;height:6px">Contact Us ›</div>
  </header>

  <div class="photo" style="top:20px;left:0;width:126px;height:145px;background:radial-gradient(ellipse at 70% 60%,rgba(40,80,25,.7),transparent 60%),linear-gradient(180deg,#a9c8dc 0%,#8fb3b9 25%,#6f9a55 45%,#4a7a30 70%,#7a5a3a 100%)" role="img" aria-label="Plantain plantation rows under a blue sky"></div>
  <div class="photo" style="top:20px;left:126px;width:126px;height:145px;background:radial-gradient(circle at 30% 80%,#b86a3a,transparent 45%),radial-gradient(circle at 75% 70%,#a65a2c,transparent 40%),linear-gradient(170deg,#5a4a3a 0%,#8c5a34 45%,#6a3418 100%)" role="img" aria-label="Trays of fresh brown eggs on a farm line"></div>
  <div class="abs center h-sans" style="top:85px;font-size:10px;color:#fff">Integrated Agriculture.<br>Nourishing Lives.</div>
  <div class="abs center" style="top:111px;font-size:3.6px;color:#fff;line-height:1.4">From our farm to your table, we deliver natural,<br>high-quality products</div>
  <div class="btn" style="left:98px;top:123px;width:27px;height:6px">Explore Products ›</div>
  <div class="btn" style="left:128px;top:123px;width:25px;height:6px">About Tallvex ›</div>
  <svg class="abs" style="top:128px;left:0" width="252" height="40" viewBox="0 0 252 40">
    <path d="M0 10 Q120 48 252 6 V40 H0Z" fill="#fff"/>
    <path d="M60 30 Q150 36 240 22" stroke="var(--lime)" stroke-width="1.4" fill="none"/>
  </svg>

  <div class="abs center script" style="top:170px;font-size:5px;color:var(--ink)">Welcome to Morrowdale Farms Limited (Tallvex)</div>
  <div class="abs center h-sans" style="top:178px;font-size:7.5px">A Nigerian integrated agribusiness<br>and premium food company</div>

  <div class="abs" style="left:31px;top:206px;width:92px;height:50px;background:var(--lime-bright);border-radius:8px">
    <div class="abs" style="left:7px;top:14px;width:20px;height:20px;border-radius:50%;background:radial-gradient(circle at 50% 40%,#8a6a55,#4a3a30)" role="img" aria-label="Portrait of the executive chairman"></div>
    <div class="abs" style="left:31px;top:13px;width:54px;font-size:2.1px;line-height:1.5;color:var(--forest)">"We are committed to producing premium quality food, creating value for our partners, empowering communities, and building a sustainable future for generations to come."</div>
    <div class="abs" style="left:31px;top:33px;font-size:2.2px;font-weight:700;color:var(--forest)">Daniel Okafor | Executive Chairman</div>
  </div>
  <div class="abs" style="left:31px;top:261px;width:92px;height:50px;background:var(--forest);border-radius:8px">
    <div class="abs" style="left:10px;top:9px;font-size:2px;font-weight:700;letter-spacing:.4px;color:#fff">OVERVIEW</div>
    <div class="abs" style="left:10px;top:16px;width:72px;font-size:2.1px;line-height:1.6;color:#dfe8d6">Dedicated to delivering high-quality food products that promote health, nutrition, and sustainable living. From poultry farming and food processing to the production of healthy snacks and natural products, we are committed to excellence across every stage of our value chain.</div>
    <div class="abs" style="left:78px;top:39px;width:6px;height:6px;border-radius:50%;background:#fff"></div>
  </div>
  <div class="photo" style="left:128px;top:206px;width:92px;height:105px;border-radius:10px;background:radial-gradient(ellipse at 70% 45%,#d9702c,transparent 45%),radial-gradient(ellipse at 40% 85%,#8fb34a,transparent 45%),linear-gradient(175deg,#9aa092 0%,#7a7f70 30%,#b8622a 60%,#5e7a32 100%)" role="img" aria-label="Processing staff sorting plantains on a factory line"></div>

  <div class="abs" style="left:0;top:325px;width:252px;height:170px;background:var(--forest)"></div>
  <svg class="abs" style="left:0;top:318px" width="252" height="22" viewBox="0 0 252 22"><path d="M0 20 Q130 -2 252 0 V0 H0Z" fill="#fff"/><path d="M20 16 Q80 20 120 14" stroke="var(--lime)" stroke-width="1.2" fill="none"/></svg>
  <div class="abs center" style="top:360px;font-size:7.5px;font-weight:600;color:#fff">Our Product Range</div>
  <div class="abs center" style="top:371px;font-size:2.6px;color:#dfe8d6">Natural Resources. Premium Products</div>
  <div class="abs" style="left:32px;top:383px;width:44px;height:44px;border-radius:50%;background:radial-gradient(circle,#c98b5a 0%,#e3b48a 35%,#f5f1ea 65%);border:1.5px solid #fff" role="img" aria-label="Tray of premium eggs"></div>
  <div class="abs" style="left:80px;top:383px;width:44px;height:44px;border-radius:50%;background:radial-gradient(circle,#c9ae3a 0%,#e6d98a 35%,#f5f1ea 65%);border:1.5px solid #fff" role="img" aria-label="Pack of plantain chips"></div>
  <div class="abs" style="left:128px;top:383px;width:44px;height:44px;border-radius:50%;background:radial-gradient(circle,#c8641a 0%,#e0a060 35%,#f5f1ea 65%);border:1.5px solid #fff" role="img" aria-label="Bottle of pure honey"></div>
  <div class="abs" style="left:176px;top:383px;width:44px;height:44px;border-radius:50%;background:radial-gradient(circle,#b2dc55,#6aa82a 60%,#4f8a1e)" role="img" aria-label="Green crop field for future products"></div>
  <div class="abs" style="left:22px;top:432px;width:64px;text-align:center;font-size:2.6px;color:#fff">Premium Eggs<div style="font-size:2px;color:#cfdcc5">Freshness, Nutritious,<br>Wholesome</div></div>
  <div class="abs" style="left:70px;top:432px;width:64px;text-align:center;font-size:2.6px;color:#fff">Plantain Chips<div style="font-size:2px;color:#cfdcc5">Real Plantain,<br>Real Taste</div></div>
  <div class="abs" style="left:118px;top:432px;width:64px;text-align:center;font-size:2.6px;color:#fff">Pure Honey<div style="font-size:2px;color:#cfdcc5">Sourced From Nature,<br>Packed From Goodness</div></div>
  <div class="abs" style="left:166px;top:432px;width:64px;text-align:center;font-size:2.6px;color:#fff">Future Products<div style="font-size:2px;color:#cfdcc5">Developing new products to<br>meet evolving customer needs</div></div>
  <div class="btn" style="left:112px;top:452px;width:28px;height:6px">Explore Products ›</div>

  <div class="abs" style="left:0;top:490px;width:252px;height:130px;background:var(--mist)"></div>
  <svg class="abs" style="left:0;top:480px" width="252" height="22" viewBox="0 0 252 22"><path d="M0 6 Q120 -4 252 20 V0 H0Z" fill="var(--forest)"/><path d="M180 18 Q220 22 252 18" stroke="var(--lime)" stroke-width="1" fill="none"/></svg>
  <div class="abs center" style="top:499px;font-size:7.5px;font-weight:600;color:var(--forest)">Our Integrated Value Chain</div>
  <div class="abs center" style="top:510px;font-size:2.4px;line-height:1.5;color:var(--ink)">At Tallvex, we manage every step of the value chain with care,<br>responsibility, and a commitment to quality.</div>
  <div class="photo" style="left:31px;top:527px;width:44px;height:62px;border-radius:4px;background:radial-gradient(ellipse at 50% 45%,#9fcf4a,transparent 55%),linear-gradient(#6fa33a,#2f5a1c)" role="img" aria-label="Plantain farming"></div>
  <div class="photo" style="left:79px;top:527px;width:44px;height:62px;border-radius:4px;background:radial-gradient(ellipse at 55% 60%,#b0603a,transparent 50%),linear-gradient(#9a7560,#4f2d1c)" role="img" aria-label="Poultry"></div>
  <div class="photo" style="left:128px;top:527px;width:44px;height:62px;border-radius:4px;background:radial-gradient(ellipse at 50% 35%,#f0b83a,transparent 55%),linear-gradient(#d99a2a,#5a4a30)" role="img" aria-label="Food processing"></div>
  <div class="photo" style="left:176px;top:527px;width:44px;height:62px;border-radius:4px;background:radial-gradient(ellipse at 55% 60%,#f4f6f7,transparent 55%),linear-gradient(#c9d0d4,#5f6a6f)" role="img" aria-label="Delivery van"></div>
  <div class="abs" style="left:37px;top:581px;font-size:3px;color:#fff">Plantain Farming</div>
  <div class="abs" style="left:86px;top:581px;font-size:3px;color:#fff">Poultry</div>
  <div class="abs" style="left:134px;top:581px;font-size:3px;color:#fff">Food Processing</div>
  <div class="abs" style="left:182px;top:581px;font-size:3px;color:#fff">Delivery</div>
  <svg class="abs" style="left:18px;top:553px" width="6" height="10"><path d="M5 1 L1 5 L5 9" stroke="#333" stroke-width=".6" fill="none"/></svg>
  <svg class="abs" style="left:228px;top:553px" width="6" height="10"><path d="M1 1 L5 5 L1 9" stroke="#333" stroke-width=".6" fill="none"/></svg>
  <div class="btn" style="left:110px;top:600px;width:32px;height:6px">See Our Value Chain ›</div>

  <div class="photo" style="left:31px;top:629px;width:189px;height:91px;border-radius:8px;background:radial-gradient(ellipse at 72% 55%,#5b4636,transparent 25%),radial-gradient(ellipse at 70% 85%,#a7cf4a,transparent 35%),linear-gradient(90deg,#8fbd52,#5a8a30 55%,#3a6a26)" role="img" aria-label="Smiling farmer holding a bunch of plantains"></div>
  <div class="abs" style="left:41px;top:639px;width:76px;height:74px;background:#fff;border-radius:8px">
    <div class="kicker abs" style="left:8px;top:14px">Community. Growth. Impact</div>
    <div class="abs h-sans" style="left:8px;top:20px;font-size:7.5px;line-height:1.25">Real Impact.<br>Lasting Change.</div>
    <div class="abs" style="left:8px;top:41px;width:62px;font-size:2.6px;line-height:1.5;color:var(--ink)">Together, we are building resilient communities and a sustainable future.</div>
    <div class="btn" style="left:8px;top:52px;width:22px;height:6px">Community ›</div>
  </div>

  <div class="photo" style="left:31px;top:754px;width:54px;height:80px;border-radius:8px;background:linear-gradient(#8bb7d8 0%,#b9d2e0 25%,#6f8f7a 40%,#4b7a3a 60%,#2e5323)" role="img" aria-label="Green mountain landscape"></div>
  <div class="photo" style="left:88px;top:754px;width:44px;height:35px;border-radius:0 10px 0 10px;background:radial-gradient(ellipse at 50% 60%,#4f8a32,transparent 50%),linear-gradient(#2d5a22,#174215)" role="img" aria-label="Young seedling in soil"></div>
  <div class="abs" style="left:88px;top:792px;width:44px;height:42px;border-radius:50%;background:var(--lime-bright)" role="img" aria-label="Globe held in hands icon"></div>
  <div class="kicker abs" style="left:145px;top:758px">Sustainability</div>
  <div class="abs h-sans" style="left:145px;top:763px;font-size:7.5px;line-height:1.25">Building a<br>Better Future</div>
  <div class="abs tiny" style="left:145px;top:785px;width:76px;font-size:2px;color:var(--ink)">At Morrowdale Farms, sustainability is at the heart of everything we do. We are committed to responsible practices that nurture our planet, support communities, and ensure a prosperous future for all.</div>
  <div class="btn" style="left:145px;top:800px;width:24px;height:6px">Sustainability ›</div>
  <div class="abs" style="left:145px;top:813px;width:76px;height:.4px;background:#999"></div>
  <div class="abs script" style="left:145px;top:818px;font-size:3.4px;line-height:1.3">Together, We grow responsibly.<br>Together, We sustain.</div>

  <div class="abs" style="left:0;top:850px;width:252px;height:170px;background:var(--mist)"></div>
  <svg class="abs" style="left:0;top:845px" width="252" height="20" viewBox="0 0 252 20"><path d="M0 0 H252 V4 Q130 18 0 6Z" fill="#fff"/><path d="M130 15 Q200 14 250 6" stroke="var(--lime)" stroke-width="1.2" fill="none"/></svg>
  <div class="abs center kicker" style="top:878px">News &amp; Media</div>
  <div class="abs center" style="top:882px;font-size:7.5px;font-weight:600;color:var(--forest)">Latest From Insights</div>
  <div class="card" style="left:31px;top:897px;width:60px;height:70px"><div style="height:40px;border-radius:4px 4px 0 0;background:radial-gradient(circle at 40% 50%,#e0a23a,transparent 55%),linear-gradient(#b4781f,#5b3812)" role="img" aria-label="Honeycomb"></div><div style="padding:3px;font-size:2.6px;font-weight:600;line-height:1.3">Fresh harvest season brings new honey range</div><div class="abs" style="left:3px;top:60px;font-size:1.8px;color:var(--orange)">AUGUST 12, 2026</div><div class="abs" style="right:3px;top:58px;width:5px;height:5px;border-radius:50%;background:var(--lime)"></div></div>
  <div class="card" style="left:96px;top:897px;width:60px;height:70px"><div style="height:40px;border-radius:4px 4px 0 0;background:radial-gradient(ellipse at 60% 60%,#3a6fb0,transparent 30%),linear-gradient(#a9c4d8,#6a9a4a 55%,#3a6a2a)" role="img" aria-label="Two agronomists reviewing a tablet in a field"></div><div style="padding:3px;font-size:2.6px;font-weight:600;line-height:1.3">Smart farming tools boost our yields</div><div class="abs" style="left:3px;top:60px;font-size:1.8px;color:var(--orange)">AUGUST 12, 2026</div><div class="abs" style="right:3px;top:58px;width:5px;height:5px;border-radius:50%;background:var(--lime)"></div></div>
  <div class="card" style="left:161px;top:897px;width:60px;height:70px"><div style="height:40px;border-radius:4px 4px 0 0;background:radial-gradient(ellipse at 45% 50%,#c08a5a,transparent 40%),linear-gradient(#8a5a36,#4a2c18)" role="img" aria-label="Poultry farmer smiling among hens"></div><div style="padding:3px;font-size:2.6px;font-weight:600;line-height:1.3">Supporting local poultry farmers nationwide</div><div class="abs" style="left:3px;top:60px;font-size:1.8px;color:var(--orange)">AUGUST 12, 2026</div><div class="abs" style="right:3px;top:58px;width:5px;height:5px;border-radius:50%;background:var(--lime)"></div></div>
  <div class="btn" style="left:110px;top:977px;width:32px;height:6px">See All News &amp; Media ›</div>

  <div class="photo" style="left:0;top:995px;width:252px;height:164px;background:linear-gradient(180deg,#4d8a38 0%,#3a7028 20%,var(--forest) 45%,var(--forest-deep))" role="img" aria-label="Misty green hills at dawn"></div>
  <svg class="abs" style="left:0;top:990px" width="252" height="30" viewBox="0 0 252 30"><path d="M0 0 H252 V2 Q140 6 0 28Z" fill="var(--mist)"/><path d="M0 24 Q60 14 130 12" stroke="var(--lime)" stroke-width="1" fill="none"/></svg>
  <div class="abs center" style="top:1022px;font-size:7.5px;font-weight:600;color:#fff;line-height:1.3">Building Today. Growing Tomorrow.<br>Feeding the World</div>
  <div class="abs center" style="top:1044px;font-size:2.6px;color:#e3ecd9">Contact us today to schedule a consultation with one of our experts.</div>
  <div class="btn" style="left:114px;top:1052px;width:22px;height:6px">Contact Us ›</div>
  <div class="abs" style="left:31px;top:1069px;width:189px;height:59px;border-radius:8px;background:rgba(255,255,255,.06);border:.4px solid rgba(255,255,255,.15)">
    <div class="abs logo" style="left:12px;top:8px;font-size:7px;color:#fff">Tallvex</div>
    <div class="abs" style="left:12px;top:19px;font-size:2.2px;color:#fff">Growing Nature. Nourishing Lives</div>
    <div class="abs" style="left:12px;top:26px;display:flex;gap:2px"><span style="width:10px;height:3px;border:.3px solid #fff"></span><span style="width:10px;height:3px;border:.3px solid #fff"></span></div>
    <div class="abs" style="left:12px;top:31px;display:flex;gap:2px"><span style="width:10px;height:3px;border:.3px solid #fff"></span><span style="width:10px;height:3px;border:.3px solid #fff"></span></div>
    <div class="abs footer-col" style="left:75px;top:7px"><h4>Navigation</h4><p>Home<br>About Us<br>Products<br>Our Business<br>Sustainability</p></div>
    <div class="abs footer-col" style="left:107px;top:7px"><h4>Quick Links</h4><p>Investors<br>News &amp; Media<br>Careers<br>Contact Us</p></div>
    <div class="abs footer-col" style="left:139px;top:7px"><h4>Contact Info</h4><p>12 Palm Grove Road, GRA,<br>Ikeja, Lagos, Nigeria.</p><p style="color:var(--lime);font-size:3px;margin-top:2px">+234 800 000 1234<br>info@tallvex.food</p></div>
  </div>
  <div class="abs center" style="top:1134px;font-size:2px;color:#cfdcc5">© 2026 · Tallvex · Morrowdale Farms Limited</div>
</section>

<section class="page page-b">
  <div class="photo" style="left:0;top:0;width:284px;height:160px;background:radial-gradient(ellipse at 75% 20%,#fff6d0,transparent 50%),linear-gradient(180deg,#fbfbf3 0%,#eef2d8 40%,#d6e0a8 100%)" role="img" aria-label="Sunlit farm field backdrop"></div>
  <header class="abs" style="left:0;top:0;width:284px;height:21px;background:#fff">
    <div class="abs logo" style="left:36px;top:5px;font-size:8px">Tallvex</div>
    <div class="abs nav-links" style="left:69px;top:9px;font-size:2.2px;gap:5px"><span>Home</span><span>About Us</span><span>Products</span><span>Our Business</span><span>Sustainability</span><span>Investors</span><span>News &amp; Media</span><span>Careers</span></div>
    <div class="btn" style="left:218px;top:7px;width:31px;height:8px;border-radius:2px">Contact Us ›</div>
  </header>
  <div class="abs h-serif" style="left:35px;top:52px;font-size:9px">Integrated Agriculture.</div>
  <div class="abs h-serif" style="left:35px;top:63px;font-size:13px;font-style:italic">Nourishing Lives.</div>
  <div class="abs" style="left:35px;top:83px;font-size:3px;line-height:1.5;color:var(--ink)">From our farm to your table, we deliver natural,<br>high-quality products.</div>
  <div class="btn" style="left:35px;top:107px;width:31px;height:8px;border-radius:2px">Explore Products ›</div>
  <div class="btn-ghost" style="left:69px;top:107px;width:33px;height:8px;background:#fff">About Tallvex ›</div>
  <div class="photo" style="left:146px;top:38px;width:56px;height:120px;border-radius:28px;background:radial-gradient(ellipse at 50% 30%,#8a6a4a,transparent 45%),radial-gradient(ellipse at 50% 75%,#d8a860,transparent 40%),linear-gradient(#4e4a34,#a0703f 60%,#5a3a22)" role="img" aria-label="Family sharing a meal at the table"></div>
  <div class="photo" style="left:206px;top:38px;width:43px;height:69px;border-radius:22px;background:radial-gradient(circle at 35% 35%,#e2925a,transparent 35%),radial-gradient(circle at 65% 70%,#d07a40,transparent 35%),linear-gradient(#a85a2e,#6a3418)" role="img" aria-label="Fresh brown eggs"></div>
  <div class="photo" style="left:206px;top:112px;width:43px;height:46px;border-radius:50%;background:linear-gradient(#f0d070 0%,#c4b84a 30%,#7aa23a 55%,#3f6e22)" role="img" aria-label="Farmland at sunset"></div>

  <svg class="abs" style="left:0;top:0" width="284" height="291" viewBox="0 0 284 291">
    <path d="M0 140 C60 120 120 150 170 185 C215 215 255 205 284 178 V251 Q284 291 244 291 H0Z" fill="var(--forest)"/>
    <path d="M100 155 C140 170 175 200 205 208 C240 215 265 200 284 182" stroke="var(--lime)" stroke-width="3" fill="none"/>
  </svg>
  <div class="abs" style="left:36px;top:208px;font-size:2.4px;color:#dfe8d6">Our Story</div>
  <div class="abs h-serif" style="left:36px;top:213px;font-size:7px;color:#fff">About Morrowdale Farms</div>
  <div class="abs" style="left:36px;top:224px;width:108px;font-size:2.1px;line-height:1.6;color:#dfe8d6">Morrowdale Farms started in a sloppy community in Ogun state, Nigeria, with one strategic goal — "To guarantee a daily and consistent supply of fresh organic food on your tables and kitchen." Since start-up, our operations have been driven by our core value of practicing sustainable farming. This has been the pillars of our growth strategy, as good custodian of the land and God's given natural resources. We are also engaging the local community to be part of our story by providing them with employment and professional advisory services for local subsistence farmers. We current operate farms in Ogun state and Lagos state, in Nigeria.</div>
  <div class="btn" style="left:36px;top:264px;width:33px;height:8px;border-radius:2px">Read Full Story ›</div>
  <div class="photo" style="left:160px;top:236px;width:28px;height:44px;border-radius:14px;background:linear-gradient(#c7c146,#6b8f2a 60%,#3f6a1e)" role="img" aria-label="Crop field view"></div>
  <div class="photo" style="left:194px;top:204px;width:34px;height:80px;border-radius:17px;background:linear-gradient(#f0c75a 0%,#bcb440 35%,#6b9a2a 70%,#3f6a1e)" role="img" aria-label="Hillside farm view"></div>
  <div class="photo" style="left:234px;top:258px;width:26px;height:33px;border-radius:13px 13px 0 0;background:linear-gradient(#c9a84a,#5b7f22)" role="img" aria-label="Sunrise field view"></div>

  <div class="abs" style="left:0;top:330px;width:284px;height:233px;background:var(--forest);border-bottom-right-radius:42px"></div>
  <div class="abs" style="left:0;top:291px;width:284px;height:119px;background:var(--mist);border-bottom-left-radius:42px"></div>
  <div class="abs h-serif" style="left:36px;top:324px;font-size:7.5px">Our Product<br>Range</div>
  <div class="abs" style="left:36px;top:346px;font-size:2.8px;line-height:1.5">Natural Resources.<br>Premium Products</div>
  <div class="btn" style="left:36px;top:362px;width:39px;height:8px;border-radius:2px">View More Products ›</div>
  <div class="card" style="left:104px;top:314px;width:45px;height:66px;border-radius:2px"><div class="abs" style="left:8px;top:8px;width:29px;height:22px;border-radius:2px;background:radial-gradient(circle at 50% 40%,#c98b5a,#e9dccb 75%)" role="img" aria-label="Egg crate"></div><div class="abs h-serif" style="left:0;right:0;top:40px;text-align:center;font-size:3px;color:var(--ink)">Premium Eggs</div><div class="abs tiny" style="left:0;right:0;top:45px;text-align:center;font-size:2px">Freshness, Nutritious,<br>Wholesome</div></div>
  <div class="card" style="left:154px;top:314px;width:45px;height:66px;border-radius:2px"><div class="abs" style="left:10px;top:8px;width:25px;height:22px;border-radius:2px;background:radial-gradient(circle at 50% 55%,#e0c44a,#8aaa3a 80%)" role="img" aria-label="Plantain chips pack"></div><div class="abs h-serif" style="left:0;right:0;top:40px;text-align:center;font-size:3px;color:var(--ink)">Plantain Chips</div><div class="abs tiny" style="left:0;right:0;top:45px;text-align:center;font-size:2px">Real Plantain,<br>Real Taste</div></div>
  <div class="card" style="left:204px;top:314px;width:45px;height:66px;border-radius:2px"><div class="abs" style="left:16px;top:6px;width:13px;height:26px;border-radius:4px;background:linear-gradient(#e8a030,#a5531a)" role="img" aria-label="Honey bottle"></div><div class="abs h-serif" style="left:0;right:0;top:40px;text-align:center;font-size:3px;color:var(--ink)">Pure Honey</div><div class="abs tiny" style="left:0;right:0;top:45px;text-align:center;font-size:2px">Sourced From Nature,<br>Packed From Goodness</div></div>

  <div class="abs center h-serif" style="top:427px;font-size:7.5px;color:#fff">Our Integrated Value Chain</div>
  <div class="abs center" style="top:438px;font-size:2.5px;line-height:1.5;color:#dfe8d6">At Tallvex, we manage every step of the value chain with care,<br>responsibility, and a commitment to quality.</div>
  <div class="photo" style="left:36px;top:463px;width:54px;height:59px;border-radius:2px;background:radial-gradient(ellipse at 40% 60%,#c06a3a,transparent 45%),linear-gradient(#9a6a55,#4a2a1a)" role="img" aria-label="Hands collecting eggs"></div>
  <div class="card" style="left:77px;top:475px;width:50px;height:38px;border-radius:2px;padding:4px"><div class="h-serif" style="font-size:3px;color:var(--ink)">Poultry</div><div class="tiny" style="font-size:1.9px;margin-top:1px">Modern, humane poultry houses delivering fresh, safe eggs to homes and retailers every day.</div><div style="font-size:1.9px;color:var(--orange);margin-top:2px">Learn More ›</div></div>
  <div class="photo" style="left:137px;top:463px;width:54px;height:59px;border-radius:2px;background:radial-gradient(ellipse at 45% 45%,#a9d855,transparent 55%),linear-gradient(#6fa33a,#2f5a1c)" role="img" aria-label="Green plantain bunches"></div>
  <div class="card" style="left:178px;top:475px;width:50px;height:38px;border-radius:2px;padding:4px"><div class="h-serif" style="font-size:3px;color:var(--ink)">Plantain Farming</div><div class="tiny" style="font-size:1.9px;margin-top:1px">Well managed plantations grown with care to supply fresh plantain for our snacks.</div><div style="font-size:1.9px;color:var(--orange);margin-top:2px">Learn More ›</div></div>
  <div class="photo" style="left:238px;top:463px;width:46px;height:59px;border-radius:2px 0 0 2px;background:radial-gradient(ellipse at 40% 40%,#f0b83a,transparent 55%),linear-gradient(#d99a2a,#5a4a30)" role="img" aria-label="Plantain chips on processing line"></div>
  <div class="abs" style="left:36px;top:540px;width:213px;height:.6px;background:rgba(255,255,255,.3)"></div>
  <div class="abs" style="left:36px;top:539.5px;width:58px;height:1.5px;background:var(--lime)"></div>
  <div class="abs" style="left:92px;top:538px;width:4px;height:4px;border-radius:50%;background:var(--lime)"></div>

  <div class="photo" style="left:0;top:563px;width:284px;height:130px;background:radial-gradient(ellipse at 85% 80%,#d6e2b8,transparent 50%),linear-gradient(90deg,#eef3e0 0%,#e3ecd0 100%);border-bottom-left-radius:40px" role="img" aria-label="Faded plantain field backdrop"></div>
  <div class="photo" style="left:40px;top:583px;width:94px;height:94px;border-radius:50%;background:radial-gradient(ellipse at 50% 75%,#4f8a2a,transparent 55%),linear-gradient(#cfe0ea 0%,#9fbf9a 25%,#5e8f34 45%,#2e5a1e);border:2px solid var(--orange);border-bottom-color:transparent;border-right-color:transparent" role="img" aria-label="Plantain plantation from above"></div>
  <div class="abs" style="left:159px;top:603px;font-size:2.2px;color:var(--orange)">Sustainability</div>
  <div class="abs h-serif" style="left:159px;top:608px;font-size:7.5px">Building a better future</div>
  <div class="abs" style="left:159px;top:619px;width:90px;font-size:2.1px;line-height:1.6;color:var(--ink)">At Morrowdale Farms, sustainability is at the heart of everything we do. We are committed to responsible practices that nurture our planet, support communities, and ensure a prosperous future for all.</div>
  <div class="btn" style="left:159px;top:637px;width:28px;height:8px;border-radius:2px">Learn More ›</div>

  <div class="abs" style="left:35px;top:706px;width:214px;height:95px;background:var(--forest);border-radius:0 30px 0 30px;overflow:hidden">
    <div class="photo" style="left:102px;top:0;width:112px;height:95px;background:radial-gradient(ellipse at 50% 40%,#4a4236,transparent 22%),radial-gradient(ellipse at 50% 80%,#a7cf4a,transparent 35%),linear-gradient(90deg,#5a8a34,#3a6a26 50%,#7fae46)" role="img" aria-label="Farmer carrying fresh plantains in the field"></div>
    <div class="abs" style="left:19px;top:24px;font-size:2.2px;color:#dfe8d6">Community. growth. Impact</div>
    <div class="abs h-serif" style="left:19px;top:29px;font-size:7.5px;color:#fff">Real Impact.<br>Lasting Change.</div>
    <div class="abs" style="left:19px;top:52px;width:64px;font-size:2.1px;line-height:1.5;color:#dfe8d6">Together, we are building resilient communities and a sustainable future.</div>
    <div class="btn" style="left:19px;top:63px;width:28px;height:8px;border-radius:2px">Learn More ›</div>
  </div>

  <div class="photo" style="left:0;top:880px;width:284px;height:200px;background:radial-gradient(ellipse at 75% 30%,#6a4e3e,transparent 25%),radial-gradient(ellipse at 20% 75%,#d8a040,transparent 30%),linear-gradient(120deg,#c7ccbf,#9a9f90 50%,#6b5a48)" role="img" aria-label="Young woman smiling while working on a laptop"></div>
  <div class="abs" style="left:0;top:814px;width:284px;height:110px;background:var(--mist);border-bottom-right-radius:40px"></div>
  <div class="abs" style="left:36px;top:842px;font-size:2.2px;color:var(--orange)">News &amp; Media holding</div>
  <div class="abs h-serif" style="left:36px;top:846px;font-size:7.5px">Latest From<br>Insights</div>
  <div class="abs" style="left:36px;top:865px;width:58px;font-size:2.6px;line-height:1.5">Get the latest must-know news, stories, and insights across our industries.</div>
  <div class="btn" style="left:36px;top:884px;width:24px;height:8px;border-radius:2px">View All ›</div>
  <div class="card" style="left:107px;top:831px;width:67px;height:78px;border-radius:2px"><div class="abs" style="left:4px;top:4px;width:59px;height:28px;background:radial-gradient(ellipse at 65% 60%,#3a6fb0,transparent 30%),linear-gradient(#a9c4d8,#6a9a4a 55%,#3a6a2a)" role="img" aria-label="Agronomists reviewing crops"></div><div class="abs" style="left:5px;top:36px;font-size:1.8px">25 Mar 2026</div><div class="abs h-serif" style="left:5px;top:40px;font-size:2.8px;color:var(--ink)">News Title goes here</div><div class="abs tiny" style="left:5px;top:45px;width:56px;font-size:1.9px;color:var(--ink)">Short summary of the story with key details and a clear takeaway for readers.</div><div class="abs" style="left:5px;top:66px;width:52px;height:.3px;background:#aaa"></div><div class="abs" style="left:58px;top:64px;width:5px;height:5px;border-radius:50%;background:var(--orange)"></div></div>
  <div class="card" style="left:181px;top:831px;width:68px;height:78px;border-radius:2px"><div class="abs" style="left:4px;top:4px;width:60px;height:28px;background:radial-gradient(ellipse at 45% 50%,#c08a5a,transparent 40%),linear-gradient(#8a5a36,#4a2c18)" role="img" aria-label="Poultry farmer among hens"></div><div class="abs" style="left:5px;top:36px;font-size:1.8px">25 Mar 2026</div><div class="abs h-serif" style="left:5px;top:40px;font-size:2.8px;color:var(--ink)">News Title goes here</div><div class="abs tiny" style="left:5px;top:45px;width:56px;font-size:1.9px;color:var(--ink)">Short summary of the story with key details and a clear takeaway for readers.</div><div class="abs" style="left:5px;top:66px;width:52px;height:.3px;background:#aaa"></div><div class="abs" style="left:59px;top:64px;width:5px;height:5px;border-radius:50%;background:var(--orange)"></div></div>

  <div class="abs" style="left:34px;top:945px;width:90px;height:90px;border-radius:50%;background:#fff;border-top:2px solid var(--orange);border-right:2px solid var(--orange)"></div>
  <div class="abs" style="left:50px;top:967px;font-size:2.2px;color:var(--orange)">Get in touch</div>
  <div class="abs h-serif" style="left:50px;top:972px;font-size:7.5px">Let's Create<br>Better Together.</div>
  <div class="abs" style="left:50px;top:990px;width:40px;height:1px;background:var(--lime)"></div>
  <div class="abs" style="left:50px;top:995px;width:60px;font-size:2.5px;line-height:1.5">Want to get in touch? We'd love to hear from you.</div>
  <div class="btn" style="left:50px;top:1008px;width:27px;height:8px;border-radius:2px">Contact us ›</div>
  <svg class="abs" style="left:0;top:1000px" width="284" height="159" viewBox="0 0 284 159">
    <path d="M0 55 C50 110 130 105 200 60 C240 35 265 25 284 20 V159 H0Z" fill="var(--forest)"/>
    <path d="M10 70 C60 110 140 100 200 62 C240 38 265 28 284 22" stroke="var(--lime)" stroke-width="2.5" fill="none"/>
  </svg>
  <div class="abs logo" style="left:36px;top:1090px;font-size:8px;color:#fff">Tallvex</div>
  <div class="abs" style="left:36px;top:1102px;font-size:2.2px;color:#fff">Growing Nature. Nourishing Lives</div>
  <div class="abs" style="left:36px;top:1107px;display:flex;gap:3px"><span style="width:3px;height:3px;border-radius:50%;background:#fff"></span><span style="width:3px;height:3px;border-radius:50%;background:#fff"></span><span style="width:3px;height:3px;border-radius:50%;background:#fff"></span></div>
  <div class="abs footer-col" style="left:107px;top:1089px"><h4>Navigation</h4><p>Home<br>About Us<br>Products<br>Our Business<br>Sustainability</p></div>
  <div class="abs footer-col" style="left:159px;top:1089px"><h4>Quick Links</h4><p>Investors<br>News &amp; Media<br>Careers<br>Contact Us</p></div>
  <div class="abs footer-col" style="left:208px;top:1089px"><h4>Contact Info</h4><p>12 Palm Grove Road, GRA,<br>Ikeja, Lagos, Nigeria.</p><p style="color:var(--lime);font-size:3.4px;margin-top:2px">+234 800 000 1234<br>info@tallvex.food</p></div>
  <div class="abs" style="left:36px;top:1139px;width:213px;height:.3px;background:rgba(255,255,255,.25)"></div>
  <div class="abs center" style="top:1145px;font-size:2px;color:#cfdcc5">© 2026 · Tallvex · Morrowdale Farms Limited</div>
</section>

</body>
</html>
```